Lunelle Rosa Hair Fancy Business Card’s

I want my business cards to be elite, original and very classy. I want the business cards to match the colors of my logo and to match the design posted. I would love the design of the picture I posted

I want the card all white .
The dripping on the top of the card I want it to match the pink color in my logo that’s also posted .
I need my logo on the business card !
I need my Instagram- @lunelle.rosa.hair__
And my phone number - 555 207 3962

Target Market(s)

My target market is young woman age 23 to older woman to the age of 65
I want both older and younger women to love my design . I don’t want any cheap looking business cards

Industry/Entity Type

Hair And Beauty

Contact Information for Business Card

Add my logo
Add my Instagram- @lunelle.rosa.hair__
My number - 555 207 3962
My website- www.lunellerosahair.example

Font styles to use
Serif
Script

Colors
ffffff
e667a6
e34298

Requirements
Must have
• The business cards must have my logo, my number , my website, and my Instagram!
Nice to have
• Nice to have glitter words that match my logo
• The business cards must look classy and mature
• I want them to be very unique!!
Should not have
• Should not have any colors that doesn’t match my logo ! This is very important! Please

```html
<!DOCTYPE html>
<html lang="en">
<head>
<meta charset="utf-8">
<title>Lunelle Rosa Hair – Business Card</title>
<link rel="stylesheet" href="https://fonts.googleapis.com/css2?family=Great+Vibes&family=Montserrat:wght@400;500&family=Playfair+Display:wght@700&display=swap">
<style>
  :root {
    --pink: #e34298;
    --pink-soft: #e667a6;
    --white: #ffffff;
    --silver: #9a9a9a;
    --ink: #555555;
    --backdrop: #ececec;
  }
  * { margin: 0; padding: 0; box-sizing: border-box; }
  html, body { width: 1200px; height: 900px; overflow: hidden; }
  body {
    background: var(--backdrop);
    font-family: "Montserrat", sans-serif;
    position: relative;
  }
  .card {
    position: absolute;
    left: 280px;
    width: 640px;
    height: 366px;
    box-shadow: 0 10px 28px rgba(0,0,0,0.18);
    overflow: hidden;
  }
  .card--front { top: 50px; background: var(--pink); }
  .card--back  { top: 470px; background: var(--white); }

  .brand-name {
    font-family: "Playfair Display", serif;
    font-weight: 700;
    text-align: center;
    line-height: 1.05;
    letter-spacing: 1px;
  }
  .card--front .brand-name {
    position: absolute;
    top: 50%; left: 50%;
    transform: translate(-50%, -50%);
    color: #d9d9d9;
    font-size: 40px;
    width: 320px;
  }

  .drip-band {
    position: absolute;
    top: 0; left: 0;
    width: 100%;
    height: 86px;
    background: linear-gradient(180deg, var(--pink) 0%, var(--pink) 55%, var(--pink-soft) 100%);
  }

  .back-content {
    position: absolute;
    top: 140px; left: 0;
    width: 100%;
    display: flex;
    align-items: center;
    justify-content: center;
  }
  .card--back .brand-name {
    color: var(--pink);
    font-size: 30px;
    width: 210px;
  }
  .divider {
    width: 1.5px;
    height: 130px;
    background: var(--pink);
    margin: 0 24px;
  }
  .contact-block { width: 260px; }
  .person-name {
    font-family: "Great Vibes", cursive;
    color: var(--pink);
    font-size: 40px;
    line-height: 1;
    margin-bottom: 14px;
  }
  .contact-list { list-style: none; }
  .contact-item {
    display: flex;
    align-items: center;
    gap: 8px;
    color: var(--ink);
    font-size: 15px;
    line-height: 22px;
    letter-spacing: 0.4px;
  }
  .contact-icon { width: 15px; height: 15px; flex: none; }
</style>
</head>
<body>

<section class="card card--front" aria-label="Business card front">
  <p class="brand-name">Lunelle Rosa Hair</p>
</section>

<section class="card card--back" aria-label="Business card back">
  <div class="drip-band" role="img" aria-label="Pink paint drips running down from the top edge"></div>
  <div class="back-content">
    <p class="brand-name">Lunelle Rosa Hair</p>
    <div class="divider"></div>
    <div class="contact-block">
      <p class="person-name">Lunelle Rosa</p>
      <ul class="contact-list">
        <li class="contact-item">
          <svg class="contact-icon" viewBox="0 0 16 16" aria-hidden="true">
            <circle cx="8" cy="8" r="7" fill="none" stroke="#e34298" stroke-width="1.3"/>
            <path d="M5.3 4.6l1.4-.3.8 1.8-.9.7c.4.9 1 1.5 1.9 1.9l.7-.9 1.8.8-.3 1.4c-3 .2-5.6-2.4-5.4-5.4z" fill="#e34298"/>
          </svg>
          555 207 3962
        </li>
        <li class="contact-item">
          <svg class="contact-icon" viewBox="0 0 16 16" aria-hidden="true">
            <circle cx="8" cy="8" r="7.5" fill="#e34298"/>
          </svg>
          @lunelle.rosa.hair__
        </li>
        <li class="contact-item">
          <svg class="contact-icon" viewBox="0 0 16 16" aria-hidden="true">
            <g fill="none" stroke="#e34298" stroke-width="1.2">
              <circle cx="8" cy="8" r="7"/>
              <ellipse cx="8" cy="8" rx="3" ry="7"/>
              <line x1="1" y1="8" x2="15" y2="8"/>
            </g>
          </svg>
          www.lunellerosahair.example
        </li>
      </ul>
    </div>
  </div>
</section>

</body>
</html>
```